Tessaline Wellness Marketing Flyer

We are a new medical practice in the community and need a flyer to send to other medical offices to inform of our services. We just completed our logo with Draftmarketo and would like to incorporate that plus our marketing content into the flyer. Our medical practice has 2 divisions: (1)Mental Health/Psychiatry and (2) Migraine and Neurospasticity Management. Please see website for content and provider photos at www.TessaWellnet.com

Target Market(s)

Other Healthcare Professionals in the Community

Industry/Entity Type

Medical

Requirements
Must have
• Photos of all 5 healthcare providers, phone number, address, logo

```html
<!DOCTYPE html>
<html lang="en">
<head>
<meta charset="utf-8">
<title>Tessaline Wellness – Flyer</title>
<link href="https://fonts.googleapis.com/css2?family=Young+Serif&family=Mulish:ital,wght@0,400;0,700;1,400&display=swap" rel="stylesheet">
<style>
  :root{
    --teal:#23968a;
    --teal-dark:#1e877b;
    --leaf:#a6c65a;
    --mint:#f2f8f4;
    --white:#ffffff;
    --page:#f6f8f5;
    --photo-a:#8c9a9b;
    --photo-b:#3f4c4e;
  }
  *{margin:0;padding:0;box-sizing:border-box}
  html,body{width:1200px;height:1200px;overflow:hidden;background:var(--page)}
  body{font-family:"Mulish",sans-serif;color:var(--teal)}
  .flyer{position:absolute;left:150px;top:18px;width:900px;height:1164px;background:var(--white);overflow:hidden;box-shadow:0 2px 10px rgba(0,0,0,.08)}
  .top-bar{position:absolute;left:0;top:0;width:100%;height:17px;background:var(--teal)}
  .brand{position:absolute;left:91px;top:80px;width:300px;text-align:center}
  .brand-dot{width:88px;height:88px;border-radius:50%;background:var(--teal);margin:0 auto 18px}
  .brand-name{font-family:"Young Serif",serif;font-size:34px;line-height:1.12;letter-spacing:2px;color:var(--teal)}
  .tagline{position:absolute;left:465px;top:70px;font-family:"Young Serif",serif;font-size:30px;line-height:38px;color:var(--teal)}
  .services{position:absolute;left:465px;top:198px;font-size:20px;line-height:25px;color:var(--teal)}
  .services p{margin-bottom:9px;width:370px}
  .content{position:absolute;left:0;top:314px;width:100%;height:620px;background:var(--mint)}
  .section-title{position:absolute;left:67px;font-family:"Young Serif",serif;font-size:24px;color:var(--teal-dark)}
  .section-text{position:absolute;left:67px;font-size:15.5px;line-height:20.7px;color:var(--teal)}
  .providers{position:absolute;left:0;top:349px;width:100%}
  .provider{position:absolute;width:200px;text-align:center;transform:translateX(-50%)}
  .photo{width:137px;height:137px;border-radius:50%;margin:0 auto;background:radial-gradient(circle at 50% 40%,var(--photo-a),var(--photo-b))}
  .provider-name{font-family:"Young Serif",serif;font-size:20px;margin-top:14px;color:var(--teal-dark);white-space:nowrap}
  .credential{font-style:italic;font-size:14px;margin-top:4px;letter-spacing:.5px}
  .doctor-photo{position:absolute;left:480px;top:435px;width:137px;height:137px;border-radius:50%;background:radial-gradient(circle at 50% 45%,#c8b59a,#5b4a3a)}
  .doctor-info{position:absolute;left:637px;top:468px}
  .doctor-name{font-family:"Young Serif",serif;font-size:20px;color:var(--teal-dark)}
  .doctor-role{font-style:italic;font-size:14.5px;line-height:18px;margin-top:6px}
  .footer{position:absolute;left:0;top:934px;width:100%;height:230px;background:var(--teal);color:var(--white)}
  .footer-motto{position:absolute;left:67px;top:38px;font-family:"Young Serif",serif;font-size:26px;line-height:30px}
  .contact{position:absolute;left:341px;top:40px;font-size:16px;line-height:20px}
  .contact h3{font-size:16.5px;font-weight:700;margin-bottom:12px}
  .contact .note{font-style:italic;margin-top:6px}
  .contact .web{font-weight:700;margin-top:14px}
  .contact .web span{color:var(--leaf)}
  .phones{position:absolute;left:628px;top:40px;font-size:16px;line-height:19.5px}
  .phones dt{font-weight:700}
  .phones dd{margin-bottom:9px}
  .leaf-corner{position:absolute;left:0;bottom:0;width:130px;height:90px;background:radial-gradient(ellipse at 20% 100%,var(--leaf),rgba(166,198,90,0) 70%)}
</style>
</head>
<body>
<main class="flyer">
  <div class="top-bar"></div>

  <header>
    <div class="brand">
      <div class="brand-dot"></div>
      <div class="brand-name">TESSALINE<br>WELLNESS</div>
    </div>
    <h1 class="tagline">Helping Bodies<br>Helping Minds<br>Helping You</h1>
    <div class="services">
      <p>Mental Health and Psychiatry Services</p>
      <p>Migraine and Neurospasticity Intervention</p>
    </div>
  </header>

  <section class="content">
    <h2 class="section-title" style="top:40px">Mental Health Providers</h2>
    <p class="section-text" style="top:78px;width:720px">Bringing comprehensive evaluation, medication management and psychotherapy to the full spectrum of mental health disorders including minor, moderate and major depression, bipolar disorder, ADD/ADHD, anxiety, schizophrenia, stress or grief reactions, and others.</p>

    <div class="providers" style="top:161px">
      <div class="provider" style="left:145px"><div class="photo" role="img" aria-label="Portrait photo of Marcus Albrecht"></div><div class="provider-name">Marcus Albrecht</div><div class="credential">PMHNP - BC</div></div>
      <div class="provider" style="left:347px"><div class="photo" role="img" aria-label="Portrait photo of Dana Whitfield"></div><div class="provider-name">Dana Whitfield</div><div class="credential">PMHNP - BC</div></div>
      <div class="provider" style="left:548px"><div class="photo" role="img" aria-label="Portrait photo of Colin Marsh"></div><div class="provider-name">Colin Marsh</div><div class="credential">PMHNP - BC</div></div>
      <div class="provider" style="left:754px"><div class="photo" role="img" aria-label="Portrait photo of Evelyn Prewitt"></div><div class="provider-name">Evelyn Prewitt</div><div class="credential">PMHNP - BC</div></div>
    </div>

    <h2 class="section-title" style="top:386px">Migraine and Neurospasticity Intervention</h2>
    <p class="section-text" style="top:424px;width:365px">Injections of botulinum neurotoxin are a widely used therapeutic form of treatment for both chronic migraines and patients with involuntary muscle contractions (neurospasticity). Injections may offer up to 3 months of relief and may be combined with other pharmaceutical interventions for maximum benefit.</p>

    <div class="doctor-photo" role="img" aria-label="Portrait photo of Dr. Alan Rutledge"></div>
    <div class="doctor-info">
      <div class="doctor-name">Dr. Alan Rutledge</div>
      <div class="doctor-role">Certified family<br>practice physician</div>
    </div>
  </section>

  <footer class="footer">
    <div class="leaf-corner" role="img" aria-label="Decorative green leaves"></div>
    <p class="footer-motto">Board Certified.<br>Responsive.<br>Compassionate.</p>
    <div class="contact">
      <h3>Contact us:</h3>
      <p>412 W. Larchmont, Suite B<br>Pine Hollow, ID 83990</p>
      <p class="note">(Located adjacent to Summit<br>Care Center on Larchmont)</p>
      <p class="web">www.<span>TessaWellnet</span>.com</p>
    </div>
    <dl class="phones">
      <dt>Mental Health</dt><dd>(208) 555-0140</dd>
      <dt>Migraine and Neurospasticity</dt><dd>(208) 555-0186</dd>
      <dt>Billing Questions</dt><dd>(208) 555-0175</dd>
    </dl>
  </footer>
</main>
</body>
</html>
```